Request for Business Card Design

Hi. My name is Marlene, I am looking for a new business card design for my company, Quarrow Signal Instruments, LLC. I really like the design you did for Tarsel Venture and was hoping you could do something similar using our full logo and our mark. I am also open to any raised texture design using our mark. I have attached our full logo, which would need to be somewhere on the card, as well as the mark in both outline and full form, as well as our brand colors / guide. The card does not have to be white, as long as our logo and mark appear. I actually like darker colored business cards more, but am open to all options. If you are interested in working with me, please let me know. We would also take the business card design into letterhead design if you can do that.

```html
<!DOCTYPE html>
<html lang="en">
<head>
<meta charset="utf-8">
<title>Quarrow Signal Instruments – Business Card</title>
<link href="https://fonts.googleapis.com/css2?family=Barlow:wght@400;600;700&display=swap" rel="stylesheet">
<style>
  :root {
    --backdrop: #7f98b8;
    --charcoal: #464646;
    --charcoal-light: #555555;
    --charcoal-dark: #3d3d3d;
    --orange: #f07630;
    --white: #ffffff;
    --soft-white: #e6e6e6;
    --mark-line: rgba(255, 235, 220, 0.75);
    --mark-text: rgba(255, 240, 228, 0.85);
  }
  * { margin: 0; padding: 0; box-sizing: border-box; }
  html, body {
    width: 1200px; height: 876px; overflow: hidden;
    background: var(--backdrop);
    font-family: "Barlow", Arial, sans-serif;
  }
  .sheet {
    width: 1200px; height: 876px;
    display: flex; flex-direction: column; align-items: center; justify-content: center;
    gap: 40px;
  }
  .card {
    position: relative;
    width: 560px; height: 320px;
    overflow: hidden;
    box-shadow: 0 10px 24px rgba(30, 45, 70, 0.35);
  }
  .card--front {
    background: linear-gradient(135deg, var(--charcoal-light), var(--charcoal) 60%, var(--charcoal-dark));
  }
  .card--back {
    background: var(--orange);
    display: flex; align-items: center; justify-content: center;
  }
  .brand {
    position: absolute; top: 26px; left: 28px;
    display: flex; align-items: center; gap: 10px;
  }
  .brand__dot {
    width: 22px; height: 22px; border-radius: 50%;
    background: var(--white);
  }
  .brand__name {
    color: var(--white);
    font-weight: 700; font-size: 17px; letter-spacing: 1.5px; line-height: 22px;
    text-transform: uppercase;
  }
  .person {
    position: absolute; right: 74px; top: 160px;
    text-align: right;
  }
  .person__name {
    color: var(--white);
    font-weight: 700; font-size: 28px; letter-spacing: 1px; line-height: 34px;
    text-transform: uppercase;
  }
  .person__role {
    color: var(--soft-white);
    font-size: 16px; line-height: 20px; margin-top: 6px;
  }
  .divider {
    position: absolute; left: 0; top: 196px;
    width: 486px; height: 2px;
    background: var(--orange);
  }
  .contact {
    position: absolute; right: 150px; top: 238px;
    text-align: right; font-style: normal;
    color: var(--soft-white);
    font-size: 14px; line-height: 20px;
  }
  .back-mark {
    display: flex; flex-direction: column; align-items: center; gap: 18px;
  }
  .back-mark__ring {
    width: 150px; height: 150px; border-radius: 50%;
    border: 3px solid var(--mark-line);
  }
  .back-mark__name {
    color: var(--mark-text);
    font-weight: 600; font-size: 16px; letter-spacing: 3px;
    text-transform: uppercase;
  }
</style>
</head>
<body>
<main class="sheet">
  <section class="card card--front" aria-label="Business card front">
    <div class="brand">
      <span class="brand__dot"></span>
      <span class="brand__name">Quarrow Signal Instruments</span>
    </div>
    <div class="person">
      <p class="person__name">Marlene</p>
      <p class="person__role">Director</p>
    </div>
    <div class="divider"></div>
    <address class="contact">
      <p>48 Harlow Lane, Brackwell 40512</p>
      <p>Ph: +1 555 0142 7781</p>
      <p>email: marlene@quarrowsignal.com</p>
    </address>
  </section>

  <section class="card card--back" aria-label="Business card back">
    <div class="back-mark">
      <span class="back-mark__ring"></span>
      <span class="back-mark__name">Quarrow</span>
    </div>
  </section>
</main>
</body>
</html>
```